Logo, Web and Mobile Designs for enterprise social media platform

All the details are in the attached document, please start reading the scope document first which explains what is this project about and the details about the needed deliverables, after that please read the UI_Requirements document which will detail what is expected regarding the coded web version since this is a coded contest, it is very important that you meet the UI requirements or suggest something else but we will need to agree first before working on the coded version

Good Luck

Target Market(s)

Enterprise Social Media

Industry/Entity Type

Media

Coding

Coded - Design and coding required

Number of Pages Required

5+ page

Font styles to use
Sans Serif

Requirements
Must have
• All the must haves are listed in the scope document so please check before you start

```html
<!DOCTYPE html>
<html lang="en">
<head>
<meta charset="utf-8">
<title>Teamora – Create New Business Opportunity</title>
<link href="https://fonts.googleapis.com/css2?family=Roboto:wght@300;400;500&display=swap" rel="stylesheet">
<style>
:root{
  --page-bg:#ebebeb;
  --header-bg:#fafafa;
  --line:#dedede;
  --panel-bg:#ffffff;
  --panel-head:#f7f8fa;
  --text:#555b61;
  --text-dark:#3e4449;
  --icon:#6c7176;
  --brand:#2a9fd1;
  --blue-btn:#24a5d8;
  --orange:#ea9200;
  --badge-orange:#f39c12;
  --footer:#1e8ab7;
  --white:#ffffff;
}
*{box-sizing:border-box;margin:0;padding:0}
html,body{width:1200px;height:769px;overflow:hidden}
body{background:var(--page-bg);font-family:'Roboto',sans-serif;color:var(--text);position:relative}
.abs{position:absolute}
.topbar{left:0;top:0;width:1200px;height:70px;background:var(--header-bg);border-bottom:1px solid var(--line)}
.divider{top:0;width:1px;height:70px;background:var(--line)}
.brand{left:168px;top:14px;display:flex;align-items:center;gap:8px}
.brand-dot{width:30px;height:30px;border-radius:50%;background:var(--badge-orange)}
.brand-name{font-size:31px;font-weight:400;color:var(--brand);line-height:40px}
.user{left:746px;top:20px;display:flex;align-items:center;gap:12px}
.avatar{width:34px;height:34px;border-radius:50%;background:radial-gradient(circle at 50% 40%,#8a7a70,#3a3330)}
.user-name{font-size:16px;font-weight:300;color:var(--text-dark)}
.badge{width:20px;height:16px;border-radius:8px;color:#fff;font-size:11px;text-align:center;line-height:16px}
.panel{left:99px;top:111px;width:1001px;height:462px;background:var(--panel-bg);border:1px solid var(--line)}
.panel-head{left:0;top:0;width:999px;height:48px;background:var(--panel-head);border-bottom:1px solid var(--line)}
.panel-title{left:19px;top:16px;font-size:15px;color:var(--text-dark);letter-spacing:.1px}
.label{font-size:14px;color:var(--text)}
.field{background:#fff;border:1px solid #e3e3e3;height:39px}
.btn-upload{background:var(--blue-btn);color:#fff;font-size:14px;height:39px;width:134px;text-align:center;line-height:39px}
.date-text{font-size:11px;color:var(--text);left:18px;top:13px}
.time-num{font-size:14px;color:var(--text)}
.save{left:209px;top:378px;width:234px;height:36px;background:var(--orange);color:#fff;font-size:15px;font-weight:500;text-align:center;line-height:36px;border-radius:2px;box-shadow:0 2px 0 #c97c00}
.footer{left:0;top:621px;width:1200px;height:148px;background:var(--footer);color:#fff;text-align:center}
.socials{display:flex;justify-content:center;gap:14px;padding-top:29px}
.social{width:24px;height:24px;border-radius:4px;background:#fff}
.links{font-size:14px;font-weight:300;margin-top:14px;word-spacing:1px}
.links span{margin:0 8px}
.copy{font-size:14px;font-weight:300;margin-top:13px}
</style>
</head>
<body>
<header class="abs topbar">
  <svg class="abs" style="left:101px;top:29px" width="18" height="14"><rect y="0" width="18" height="2.5" fill="#777"/><rect y="5.5" width="18" height="2.5" fill="#777"/><rect y="11" width="18" height="2.5" fill="#777"/></svg>
  <div class="abs divider" style="left:144px"></div>
  <div class="abs brand"><div class="brand-dot"></div><span class="brand-name">Teamora</span></div>
  <div class="abs user">
    <div class="avatar" role="img" aria-label="User profile photo"></div>
    <span class="user-name">Dana Hollis</span>
    <svg width="12" height="8"><path d="M0 0h12L6 7z" fill="#555"/></svg>
  </div>
  <div class="abs divider" style="left:922px"></div>
  <svg class="abs" style="left:945px;top:26px" width="20" height="19"><g fill="#666"><rect x="0" y="0" width="9" height="5"/><rect x="0" y="7" width="20" height="5"/><rect x="0" y="14" width="9" height="5"/><rect x="11" y="14" width="9" height="5" fill="#999"/></g></svg>
  <div class="abs badge" style="left:957px;top:16px;background:var(--badge-orange)">8</div>
  <div class="abs divider" style="left:991px"></div>
  <svg class="abs" style="left:1011px;top:26px" width="20" height="20"><circle cx="8" cy="8" r="6" fill="none" stroke="#666" stroke-width="2.6"/><path d="M12.5 12.5l5.5 5.5" stroke="#666" stroke-width="3" stroke-linecap="round"/></svg>
  <div class="abs divider" style="left:1051px"></div>
  <svg class="abs" style="left:1072px;top:27px" width="18" height="19"><path d="M9 1c-4 0-6 3-6 7v4l-2 3h16l-2-3V8c0-4-2-7-6-7z" fill="#666"/><circle cx="9" cy="17" r="2" fill="#666"/></svg>
  <div class="abs badge" style="left:1079px;top:16px;background:var(--blue-btn)">8</div>
</header>

<main class="abs panel">
  <div class="abs panel-head">
    <div class="abs panel-title">CREATE NEW BUSINESS OPPORTUNITY - STEP 2</div>
    <svg class="abs" style="left:965px;top:19px" width="8" height="10"><path d="M1 1l5 4-5 4" fill="none" stroke="#aaa" stroke-width="1.6"/></svg>
  </div>

  <div class="abs label" style="left:36px;top:96px">Upload Banner Photo : *</div>
  <div class="abs field" style="left:208px;top:85px;width:386px"></div>
  <div class="abs btn-upload" style="left:594px;top:85px">UPLOADED</div>

  <div class="abs label" style="left:36px;top:151px">Upload Files : *</div>
  <div class="abs field" style="left:208px;top:140px;width:386px"></div>
  <div class="abs btn-upload" style="left:594px;top:140px">UPLOADED</div>

  <svg class="abs" style="left:208px;top:196px" width="16" height="13"><rect x=".5" y=".5" width="15" height="12" fill="none" stroke="#777"/><path d="M2 11l4-5 3 3 2-2 3 4z" fill="#777"/></svg>
  <div class="abs" style="left:233px;top:196px;font-size:13px;color:var(--text-dark)">Brightmesh-logo.png</div>

  <div class="abs label" style="left:36px;top:261px">From Date :</div>
  <div class="abs field" style="left:208px;top:249px;width:177px"><span class="abs date-text">12 - 10 - 2015</span></div>
  <div class="abs label" style="left:438px;top:261px">From Time :</div>
  <div class="abs field" style="left:550px;top:249px;width:177px">
    <span class="abs time-num" style="left:18px;top:11px">10&nbsp;&nbsp; : &nbsp;48</span>
    <div class="abs" style="left:100px;top:0;width:1px;height:37px;background:#e3e3e3"></div>
    <svg class="abs" style="left:112px;top:10px" width="10" height="18"><path d="M1 5l4-4 4 4M1 13l4 4 4-4" fill="none" stroke="#666" stroke-width="1.2"/></svg>
    <div class="abs" style="left:133px;top:0;width:1px;height:37px;background:#e3e3e3"></div>
    <span class="abs time-num" style="left:144px;top:12px">AM</span>
  </div>

  <div class="abs label" style="left:36px;top:322px">To Date :</div>
  <div class="abs field" style="left:208px;top:310px;width:177px"><span class="abs date-text">12 - 10 - 2015</span></div>
  <div class="abs label" style="left:438px;top:322px">To Time :</div>
  <div class="abs field" style="left:550px;top:310px;width:177px">
    <span class="abs time-num" style="left:18px;top:11px">10&nbsp;&nbsp; : &nbsp;48</span>
    <div class="abs" style="left:100px;top:0;width:1px;height:37px;background:#e3e3e3"></div>
    <svg class="abs" style="left:112px;top:10px" width="10" height="18"><path d="M1 5l4-4 4 4M1 13l4 4 4-4" fill="none" stroke="#666" stroke-width="1.2"/></svg>
    <div class="abs" style="left:133px;top:0;width:1px;height:37px;background:#e3e3e3"></div>
    <span class="abs time-num" style="left:144px;top:12px">AM</span>
  </div>

  <div class="abs save">SAVE AND GO TO STEP 2</div>
</main>

<footer class="abs footer">
  <div class="socials">
    <div class="social"></div><div class="social"></div><div class="social"></div><div class="social"></div><div class="social"></div>
  </div>
  <div class="links">Home<span>/</span>Contact<span>/</span>Topics<span>/</span>Posts and Comments<span>/</span>Discussion<span>/</span>Videos Links</div>
  <div class="copy">Copyright @ 2015 - 2015.Teamora. All Rights Reserved.</div>
</footer>
</body>
</html>
```